Water Management Company Letterhead

Looking for a eye-catching design of letterhead for a California based parent company of water management products. The letterhead would need to include the three logos of the sub-companies, with "The Brookline Collective LLC" (parent company) being the primary focus. Please include the sub-company logos in the following order of significance: Velmoro, Drifting Reeds North, and then Gromtile NE. The color schemes should convey water/enviornment - blues and greens. Most importantly it should be something that will stand out. All logos are uploaded. Thank you for your interest!

Target Market(s)

Environmental conservationists, government agencies, etc.

Industry/Entity Type

Environment

Font styles to use
Serif
Sans Serif

Colors
33a6d7
3276b5
abd037
cadf82
85cae6
85acd3

Requirements
Must have
• eye-catching, blue and green tones pulled from logos, water droplet.

```html
<!DOCTYPE html>
<html lang="en">
<head>
<meta charset="utf-8">
<title>The Brookline Collective LLC – Letterhead</title>
<link rel="stylesheet" href="https://fonts.googleapis.com/css2?family=Cinzel:wght@500&family=Open+Sans:wght@400;600;700&display=swap">
<style>
  :root {
    --backdrop: #e6e7e9;
    --paper: #ffffff;
    --ink: #2a2a2a;
    --ink-soft: #555b62;
    --brand-navy: #1f3350;
    --water-blue: #2a8cc8;
    --sky-blue: #33a6d7;
    --deep-blue: #3276b5;
    --leaf-green: #8cc23e;
    --signature-tone: #d9dadc;
    --watermark-tone: #ececec;
  }
  * { box-sizing: border-box; margin: 0; padding: 0; }
  html, body { width: 1200px; height: 1000px; overflow: hidden; }
  body {
    background: var(--backdrop);
    font-family: "Open Sans", Arial, sans-serif;
    color: var(--ink);
  }
  .letterhead {
    position: absolute;
    left: 240px; top: 34px;
    width: 720px; height: 932px;
    background: var(--paper);
    box-shadow: 0 6px 24px rgba(0,0,0,.12);
    overflow: hidden;
  }
  .watermark {
    position: absolute; left: 470px; top: 400px;
    width: 300px; height: 380px;
    border-radius: 50%;
    background: radial-gradient(ellipse at 50% 55%, var(--watermark-tone) 0%, var(--watermark-tone) 55%, rgba(236,236,236,0) 72%);
  }
  .contact {
    position: absolute; left: 548px; top: 40px;
    list-style: none; font-size: 8.5px; line-height: 12px; color: var(--ink-soft);
  }
  .contact li { display: flex; align-items: flex-start; gap: 6px; }
  .contact svg { flex: none; margin-top: 1px; }
  .brand {
    position: absolute; left: 56px; top: 110px;
    display: flex; align-items: center; gap: 10px;
  }
  .brand-dot {
    width: 14px; height: 14px; border-radius: 50%;
    background: var(--sky-blue);
  }
  .brand-name {
    font-family: "Cinzel", Georgia, serif;
    font-weight: 500; font-size: 26px; letter-spacing: .5px;
    color: var(--brand-navy);
    white-space: nowrap;
  }
  .recipient {
    position: absolute; left: 56px; top: 176px;
    font-size: 11px; font-weight: 700; line-height: 17px; font-style: normal;
  }
  .letter-body {
    position: absolute; left: 112px; top: 258px; width: 520px;
    font-size: 11px; line-height: 18px;
  }
  .letter-body p { margin-bottom: 22px; }
  .sign-off {
    position: absolute; left: 112px; top: 585px;
    font-size: 11px;
  }
  .signature {
    position: absolute; left: 112px; top: 608px;
    width: 150px; height: 56px; background: var(--signature-tone);
    border-radius: 4px;
  }
  .signer {
    position: absolute; left: 112px; top: 674px; font-size: 11px;
  }
  .partners {
    position: absolute; left: 0; right: 0; top: 790px;
    display: flex; justify-content: space-around; align-items: center;
    padding: 0 60px;
  }
  .partner { display: flex; align-items: center; gap: 7px; }
  .partner-mark { width: 12px; height: 12px; border-radius: 50%; background: var(--water-blue); }
  .partner-mark.square { border-radius: 0; background: var(--leaf-green); }
  .partner-name { font-size: 14px; font-weight: 600; color: var(--deep-blue); line-height: 16px; }
  .partner-tag { font-size: 7px; color: var(--ink-soft); display: block; font-weight: 400; }
  .footer-band {
    position: absolute; left: 0; right: 0; bottom: 0; height: 28px;
    display: flex;
  }
  .footer-band .band-blue { flex: 1; background: var(--water-blue); }
  .footer-band .band-gap { width: 6px; background: var(--paper); }
  .footer-band .band-green { width: 170px; background: var(--leaf-green); }
</style>
</head>
<body>
  <article class="letterhead">
    <div class="watermark" role="img" aria-label="Large faint water droplet watermark"></div>

    <ul class="contact">
      <li><svg width="10" height="10" viewBox="0 0 10 10"><rect width="10" height="10" fill="#2a8cc8"/><path d="M3 2.2c.5 1.9 1.7 3.3 4.6 4.8l-.8.9C4.4 6.8 2.8 4.9 2.2 2.8z" fill="#fff"/></svg>(000) 410-5200</li>
      <li><svg width="10" height="10" viewBox="0 0 10 10"><rect width="10" height="10" fill="#2a8cc8"/><path d="M2 3h6v4H2zM2 3l3 2 3-2" fill="none" stroke="#fff" stroke-width=".8"/></svg>hello@brooklinecollective.com</li>
      <li><svg width="10" height="10" viewBox="0 0 10 10"><rect width="10" height="10" fill="#2a8cc8"/><circle cx="5" cy="5" r="3" fill="none" stroke="#fff" stroke-width=".8"/><path d="M2 5h6M5 2v6" stroke="#fff" stroke-width=".6"/></svg>www.brooklinecollective.com</li>
      <li><svg width="10" height="10" viewBox="0 0 10 10"><rect width="10" height="10" fill="#2a8cc8"/><path d="M5 8.5C3 6 2.8 5 2.8 4.2a2.2 2.2 0 0 1 4.4 0C7.2 5 7 6 5 8.5z" fill="#fff"/></svg>Address Line 1<br>Area Name Orland, CA 95963</li>
    </ul>

    <header class="brand">
      <span class="brand-dot"></span>
      <h1 class="brand-name">The Brookline Collective LLC</h1>
    </header>

    <address class="recipient">
      To<br>Lorem Ipsum is simply<br>Lorem Ipsum is Lorem Ipsum is<br>Lorem Ipsum is
    </address>

    <section class="letter-body">
      <p>dummy text of the printing and typesetting industry. Lorem Ipsum has been the industry's standard dummy text ever since the 1500s, when an unknown printer took a galley of type and scrambled it to make a type specimen book. It has survived not only five centuries, but also the leap into electronic typesetting, remaining essentially unchanged.</p>
      <p>It is a long established fact that a reader will be distracted by the readable content of a page when looking at its layout. The point of using Lorem Ipsum is that it has a more-or-less normal distribution of letters, as opposed to using 'Content here, content here', making it look like readable English. Many desktop publishing packages and web page editors now use Lorem Ipsum as their default model text, and a search for 'lorem'.</p>
      <p>Contrary to popular belief, Lorem Ipsum is not simply random text. It has roots in a piece of classical Latin literature from 45 BC, making it over 2000 years old. Edwin Harrow, a Latin professor at Alder Ridge College in Vermont, looked up one of the more obscure Latin words, consectetur, from a Lorem Ipsum passage.</p>
    </section>

    <p class="sign-off">Lorem Ipsum</p>
    <div class="signature" role="img" aria-label="Handwritten signature"></div>
    <p class="signer">Lorem Ipsum is a dummy</p>

    <footer class="partners">
      <div class="partner"><span class="partner-mark"></span><span class="partner-name">Velmoro<span class="partner-tag">Water Distribution</span></span></div>
      <div class="partner"><span class="partner-mark"></span><span class="partner-name">Drifting Reeds North<span class="partner-tag">Floating wetland systems</span></span></div>
      <div class="partner"><span class="partner-mark square"></span><span class="partner-name">Gromtile NE<span class="partner-tag">pavers</span></span></div>
    </footer>

    <div class="footer-band">
      <span class="band-blue"></span><span class="band-gap"></span><span class="band-green"></span>
    </div>
  </article>
</body>
</html>
```